Small butcher shop from Austria needs great powerpoint presentation

We are looking for a powerpoint template for our new CI - it should be modern and clear.

Logo (2 Versions), Slogan, Business Card and Car-Wrap-Design already exist. (See documents below.)

We won't use much text. About 50% of the presentation should be pictures, included in different ways.

We are a family business in Upper Austria, only process animals from farms in the immediate vicinity, produce the products by hand, value animal welfare and short transport routes and avoid packaging as much as possible.

The design should be modern and clear.

Sans Serif

• Use the red color sparingly. Only use sans serif fonts (Myriad Pro - if possible). The logo needs to be on first and last page only.

```html
<!DOCTYPE html>
<html lang="en">
<head>
<meta charset="utf-8">
<title>Halmer Presentation Template</title>
<link rel="stylesheet" href="https://fonts.googleapis.com/css2?family=Source+Sans+3:wght@400;600;700&display=swap">
<style>
:root{
  --canvas:#7d8186;
  --wine:#6d0a17;
  --wine-bright:#b5182e;
  --slate:#5e6165;
  --ink:#1d1d1d;
  --body:#3a3a3a;
  --white:#ffffff;
  --night:#141617;
}
*{box-sizing:border-box;margin:0;padding:0}
html,body{width:1200px;height:3586px;overflow:hidden}
body{background:var(--canvas);font-family:"Source Sans 3",Arial,sans-serif;color:var(--body);position:relative}
.slide{position:absolute;left:102px;width:1002px;height:563px;overflow:hidden;background:var(--white)}
.photo{position:absolute}
h2,h3{font-weight:700;text-transform:uppercase;color:var(--ink);line-height:1.3}
p{font-size:12.5px;line-height:1.5}

/* Slide 1 */
.s-cover{top:25px}
.s-cover .photo{inset:0;background:
  radial-gradient(ellipse at 82% 28%,rgba(255,250,220,.85) 0%,rgba(255,250,220,0) 35%),
  radial-gradient(ellipse at 92% 55%,#2f4a22 0%,rgba(47,74,34,0) 40%),
  radial-gradient(ellipse at 12% 38%,#3f6a2a 0%,rgba(63,106,42,0) 35%),
  linear-gradient(180deg,#b9cad2 0%,#d7e0dc 22%,#7f9c5a 42%,#6b9a38 62%,#4f7d24 100%)}
.brand{position:absolute;left:0;right:0;top:92px;text-align:center;font-size:68px;font-weight:700;color:var(--wine);letter-spacing:4px;line-height:1}
.brand-sub{position:absolute;left:0;right:0;top:172px;text-align:center;font-size:11px;letter-spacing:4px;color:#4a4a4a}
.welcome{position:absolute;left:746px;top:440px;color:var(--white);font-weight:700;line-height:1}
.welcome span{display:block;font-size:30px}
.welcome strong{display:block;font-size:66px;margin-top:4px}

/* Slide 2 */
.s-split{top:612px}
.s-split .p1{left:0;top:0;width:501px;height:279px;background:
  radial-gradient(ellipse at 55% 45%,#a8404a 0%,rgba(168,64,74,0) 40%),
  radial-gradient(ellipse at 15% 20%,#7a3038 0%,rgba(122,48,56,0) 30%),
  linear-gradient(135deg,#4a2f22,#6a4030 50%,#2e211a)}
.s-split .p2{left:501px;top:279px;width:501px;height:284px;background:
  radial-gradient(ellipse at 45% 65%,#e8e8e6 0%,rgba(232,232,230,0) 22%),
  linear-gradient(180deg,#d5d9dd 0%,#a9adb0 45%,#4d463c 75%,#3a3028 100%)}
.s-split .t{position:absolute;width:385px}
.s-split h2{font-size:15px;margin-bottom:16px}
.s-split p{font-size:12.5px;line-height:1.5}
.s-split .t1{left:553px;top:52px}
.s-split .t2{left:56px;top:335px}

/* Slide 3 */
.s-grid{top:1199px}
.card{position:absolute;top:33px;width:221px}
.card .photo{position:relative;width:221px;height:327px}
.card h3{margin-top:15px;font-size:15px;color:var(--wine);padding-bottom:9px;border-bottom:2px solid var(--wine)}
.card p{margin-top:18px;font-size:12px}
.c1{left:22px}.c2{left:270px}.c3{left:515px}.c4{left:764px}
.c1 .photo{background:radial-gradient(ellipse at 60% 30%,#d04050 0%,rgba(208,64,80,0) 30%),radial-gradient(ellipse at 55% 72%,#c83848 0%,rgba(200,56,72,0) 30%),linear-gradient(160deg,#3a2e2a,#2a2220 60%,#1f3a22)}
.c2 .photo{background:linear-gradient(180deg,#e6dfb0 0%,#cfc48a 35%,#a08a40 60%,#6f5f2a 100%)}
.c3 .photo{background:linear-gradient(180deg,#1f55b8 0%,#4a86d6 30%,#5a8a3a 52%,#3f6a22 100%)}
.c4 .photo{background:radial-gradient(ellipse at 40% 20%,#c03a45 0%,rgba(192,58,69,0) 40%),linear-gradient(170deg,#a22a35,#7a1a28 60%,#c03a2a 92%,#d04a2a)}

/* Slide 4 */
.s-duo{top:1782px}
.half{position:absolute;top:0;height:563px}
.half.red{left:0;width:493px;background:var(--wine)}
.half.grey{left:493px;width:509px;background:var(--slate)}
.item{position:absolute;height:124px}
.item .photo{left:0;top:0;width:160px;height:124px}
.item .tx{position:absolute;left:182px;top:6px;width:230px;color:var(--white)}
.item h3{font-size:14.5px;color:var(--white)}
.item p{font-size:11.5px;margin-top:10px;color:#f0e6e6}
.red .item{left:23px}.grey .item{left:53px}
.r1{top:49px}.r2{top:220px}.r3{top:398px}
.g-a{background:radial-gradient(ellipse at 55% 55%,#c03848 0%,rgba(192,56,72,0) 45%),linear-gradient(135deg,#4a3a30,#5a4030)}
.g-b{background:radial-gradient(ellipse at 45% 70%,#b02a35 0%,rgba(176,42,53,0) 40%),linear-gradient(180deg,#5a9ad0 0%,#3a5a80 45%,#2a2a2a 100%)}
.g-c{background:radial-gradient(ellipse at 50% 75%,#8a2a30 0%,rgba(138,42,48,0) 50%),linear-gradient(180deg,#0f0f0f,#1a1a1a)}
.g-d{background:linear-gradient(100deg,#3a2a20 0%,#6a5a3a 40%,#e6dccb 70%,#8a7a5a 100%)}
.g-e{background:linear-gradient(180deg,#e8a850 0%,#b07a3a 45%,#5a3f22 100%)}
.g-f{background:linear-gradient(180deg,#1f4fb0 0%,#6a9ad0 48%,#3a9a2a 60%,#2f7a22 100%)}

/* Slide 5 */
.s-list{top:2365px}
.s-list .photo{left:419px;top:0;width:583px;height:563px;background:
  radial-gradient(ellipse at 45% 55%,rgba(240,240,240,.5) 0%,rgba(240,240,240,0) 25%),
  linear-gradient(180deg,#1f3fa8 0%,#3f68c4 50%,#7a9ad8 72%,#4a7a2a 76%,#3a6a22 100%)}
.entry{position:absolute;left:38px;width:356px}
.entry h3{font-size:15px;color:var(--wine)}
.entry p{margin-top:8px;font-size:12px}
.e1{top:141px}.e2{top:267px}.e3{top:394px}
.rule{position:absolute;left:38px;width:356px;height:1px;background:#333}
.l1{top:231px}.l2{top:359px}

/* Slide 6 */
.s-close{top:2955px;background:var(--night)}
.s-close .photo{left:0;top:175px;width:1002px;height:388px;background:
  radial-gradient(ellipse at 25% 65%,#9a2a32 0%,#6a161e 35%,rgba(40,10,12,0) 65%),
  radial-gradient(ellipse at 78% 60%,#8a2029 0%,#5a1218 38%,rgba(40,10,12,0) 68%),
  linear-gradient(180deg,rgba(20,22,23,0) 0%,#2a0d10 60%,#3a1a14 100%)}
.close-brand{position:absolute;left:26px;top:96px;font-size:66px;font-weight:700;color:var(--wine-bright);letter-spacing:4px;line-height:1}
.close-sub{position:absolute;left:58px;top:170px;font-size:10px;letter-spacing:4px;color:var(--wine-bright)}
.close-text{position:absolute;left:564px;top:42px;width:330px;color:var(--white)}
.close-text h2{font-size:17px;color:var(--white);letter-spacing:2px}
.close-text p{margin-top:10px;font-size:13px;color:#e6e6e6;letter-spacing:.6px}
</style>
</head>
<body>

<section class="slide s-cover">
  <div class="photo" role="img" aria-label="Cow grazing on a sunlit green meadow with forest"></div>
  <div class="brand">HALMER</div>
  <div class="brand-sub">FLEISCHHAUEREI</div>
  <div class="welcome"><span>WELCOME TO</span><strong>HALMER</strong></div>
</section>

<section class="slide s-split">
  <div class="photo p1" role="img" aria-label="Hands holding raw beef steak beside a cleaver on a wooden board"></div>
  <div class="t t1">
    <h2>Lorem ipsum is simply dummy text</h2>
    <p>There are many variations of passages of Lorem Ipsum available, but the majority have suffered alteration in some form, by injected humour, or randomised words which don't look even slightly believable. If you are going to use a passage of Lorem Ipsum, you need to be sure there isn't anything embarrassing hidden in the middle of text. All the Lorem Ipsum generators on the Internet tend to repeat predefined chunks as necessary, making this the first true generator on the Internet.</p>
  </div>
  <div class="t t2">
    <h2>Lorem ipsum is simply dummy text</h2>
    <p>There are many variations of passages of Lorem Ipsum available, but the majority have suffered alteration in some form, by injected humour, or randomised words which don't look even slightly believable. If you are going to use a passage of Lorem Ipsum, you need to be sure there isn't anything embarrassing hidden in the middle of text. All the Lorem Ipsum generators on the Internet tend to repeat predefined chunks as necessary, making this the first true generator on the Internet.</p>
  </div>
  <div class="photo p2" role="img" aria-label="Dairy cows standing in a farmyard in front of a barn"></div>
</section>

<section class="slide s-grid">
  <article class="card c1">
    <div class="photo" role="img" aria-label="Two raw ribeye steaks with garlic and herbs"></div>
    <h3>Lorem ipsum is simply<br>dummy text</h3>
    <p>There are many variations of passages of Lorem Ipsum available, but the majority have suffered alteration in some form, by injected humour, or randomised words which don't look.</p>
  </article>
  <article class="card c2">
    <div class="photo" role="img" aria-label="Brown cattle in golden grassland"></div>
    <h3>Lorem ipsum is simply<br>dummy text</h3>
    <p>There are many variations of passages of Lorem Ipsum available, but the majority have suffered alteration in some form, by injected humour, or randomised words which don't look.</p>
  </article>
  <article class="card c3">
    <div class="photo" role="img" aria-label="Herd of cows on a green pasture under blue sky"></div>
    <h3>Lorem ipsum is simply<br>dummy text</h3>
    <p>There are many variations of passages of Lorem Ipsum available, but the majority have suffered alteration in some form, by injected humour, or randomised words which don't look.</p>
  </article>
  <article class="card c4">
    <div class="photo" role="img" aria-label="Fresh cuts of meat in a butcher's display counter"></div>
    <h3>Lorem ipsum is simply<br>dummy text</h3>
    <p>There are many variations of passages of Lorem Ipsum available, but the majority have suffered alteration in some form, by injected humour, or randomised words which don't look.</p>
  </article>
</section>

<section class="slide s-duo">
  <div class="half red">
    <div class="item r1"><div class="photo g-a" role="img" aria-label="Raw ribeye steaks with garlic"></div><div class="tx"><h3>Lorem ipsum is simply<br>dummy text</h3><p>There are many variations of passages of Lorem Ipsum available, but the majority have suffered alteration in some form, by injected humour,.</p></div></div>
    <div class="item r2"><div class="photo g-b" role="img" aria-label="Butcher presenting a large cut of beef"></div><div class="tx"><h3>Lorem ipsum is simply<br>dummy text</h3><p>There are many variations of passages of Lorem Ipsum available, but the majority have suffered alteration in some form, by injected humour,.</p></div></div>
    <div class="item r3"><div class="photo g-c" role="img" aria-label="Raw steaks on a dark background"></div><div class="tx"><h3>Lorem ipsum is simply<br>dummy text</h3><p>There are many variations of passages of Lorem Ipsum available, but the majority have suffered alteration in some form, by injected humour,.</p></div></div>
  </div>
  <div class="half grey">
    <div class="item r1"><div class="photo g-d" role="img" aria-label="Cows feeding on hay inside a barn"></div><div class="tx"><h3>Lorem ipsum is simply<br>dummy text</h3><p>There are many variations of passages of Lorem Ipsum available, but the majority have suffered alteration in some form, by injected humour,.</p></div></div>
    <div class="item r2"><div class="photo g-e" role="img" aria-label="Brown cow in a field at sunset"></div><div class="tx"><h3>Lorem ipsum is simply<br>dummy text</h3><p>There are many variations of passages of Lorem Ipsum available, but the majority have suffered alteration in some form, by injected humour,.</p></div></div>
    <div class="item r3"><div class="photo g-f" role="img" aria-label="Cows grazing on a green meadow under blue sky"></div><div class="tx"><h3>Lorem ipsum is simply<br>dummy text</h3><p>There are many variations of passages of Lorem Ipsum available, but the majority have suffered alteration in some form, by injected humour,.</p></div></div>
  </div>
</section>

<section class="slide s-list">
  <div class="entry e1"><h3>Lorem ipsum is simply dummy text</h3><p>There are many variations of passages of Lorem Ipsum available, but the majority have suffered alteration in some form, by injected humour, or randomised words which don't look.</p></div>
  <div class="rule l1"></div>
  <div class="entry e2"><h3>Lorem ipsum is simply dummy text</h3><p>There are many variations of passages of Lorem Ipsum available, but the majority have suffered alteration in some form, by injected humour, or randomised words which don't look.</p></div>
  <div class="rule l2"></div>
  <div class="entry e3"><h3>Lorem ipsum is simply dummy text</h3><p>There are many variations of passages of Lorem Ipsum available, but the majority have suffered alteration in some form, by injected humour, or randomised words which don't look.</p></div>
  <div class="photo" role="img" aria-label="Black and white cow standing in a pasture with the herd behind, deep blue sky"></div>
</section>

<section class="slide s-close">
  <div class="photo" role="img" aria-label="Close-up of marbled raw beef cuts on a dark background"></div>
  <div class="close-brand">HALMER</div>
  <div class="close-sub">FLEISCHHAUEREI</div>
  <div class="close-text">
    <h2>Lorem ipsum is simply<br>dummy text</h2>
    <p>There are many variations of passages of Lorem Ipsum available, but the majority have suffered alteration in some form, by injected humour, or randomised words which</p>
  </div>
</section>

</body>
</html>
```